KR Appraisals website redesign

I would like to refresh my existing website of www.krappraisals-example.com with new graphics, look and feel, as well as updated structure and wording. Content and layout changes have been uploaded to this project Brief.

My existing website has a dark feel. I am now looking for a light and energetic feel. Financial Services is my industry, so the website should be reflect that. I would also like to reflect the concepts of Trust, Service and Expertise.

The website must be serious and upmarket.

Target Market(s)

Corporate board members, CFO's, treasurers and controllers
Auditors, tax advisors, private equity and venture capital asset managers, investors, tax authorities

Industry/Entity Type

Financial Service

Coding

Coded - Design and coding required

Number of Pages Required

5+ page

Font styles to use
Sans Serif
Other font styles liked:
• Designer can choose another modern font

Colors
0355a3
3277b5
85acd3
eaf1f7
f37122
f68d4d
9bcb3c
acd037
cadf82

Requirements
Must have
• Good hi resolution pictures that convey "Finance", "Trust", "Service" or "Expertise".
• An anti-bot (such as Captcha) mechanism in the contact form.
Should not have
• Must not have all content on one rolling screen.

```html
<!DOCTYPE html>
<html lang="en">
<head>
<meta charset="utf-8">
<title>KR Appraisals – Meet the Team</title>
<link href="https://fonts.googleapis.com/css2?family=Figtree:wght@400;600;700&family=Montserrat:wght@600;700&display=swap" rel="stylesheet">
<style>
:root{
  --blue:#0355a3;
  --orange:#f37122;
  --green:#9bcb3c;
  --text:#555;
  --muted:#777;
  --rule:#e2e2e2;
  --footer:#333;
  --footer-text:#aaa;
  --white:#fff;
}
*{margin:0;padding:0;box-sizing:border-box}
html,body{width:757px;height:1200px;overflow:hidden;background:var(--white)}
body{position:relative;font-family:"Figtree",sans-serif;color:var(--text)}
.site-header{position:absolute;left:0;top:0;width:757px;height:63px;
  background:linear-gradient(90deg,#e6e6dc 0%,#eceee2 50%,#f6f6e6 100%)}
.brand{position:absolute;left:102px;top:22px;display:flex;align-items:center;gap:6px;
  font-family:"Figtree",sans-serif;font-weight:600;font-size:13px;color:#8a8a8a;letter-spacing:.3px}
.brand-square{width:12px;height:12px;background:#8a8a8a}
.main-nav{position:absolute;top:29px;left:0;width:757px;height:10px}
.main-nav a{position:absolute;font-family:"Montserrat",sans-serif;font-weight:600;font-size:6.8px;color:#888;text-decoration:none;letter-spacing:.1px}
.main-nav a.active{color:var(--blue)}
.page-title{position:absolute;top:116px;left:0;width:757px;text-align:center;
  font-family:"Montserrat",sans-serif;font-weight:700;font-size:25px;color:var(--orange);letter-spacing:-.3px}
.member{position:absolute;left:102px;width:554px}
.member-photo{position:absolute;left:0;top:0;width:123px;height:123px}
.member-info{position:absolute;left:143px;top:-2px;width:411px}
.member-name{font-family:"Montserrat",sans-serif;font-weight:700;font-size:14px;color:var(--blue);line-height:18px}
.member-role{font-size:7.2px;color:var(--muted);margin-top:3px}
.member-field{font-size:7.2px;color:var(--green);margin-top:3px}
.member-bio{font-size:7.1px;line-height:12.35px;color:#666;margin-top:14px}
.divider{position:absolute;left:102px;width:554px;height:1px;background:var(--rule)}
.site-footer{position:absolute;left:0;top:976px;width:757px;height:224px}
.footer-bg{position:absolute;left:0;top:0}
.footer-brand{position:absolute;top:45px;left:0;width:757px;display:flex;justify-content:center;align-items:center;gap:6px;
  font-weight:600;font-size:13px;color:#8a8a8a;letter-spacing:.3px}
.footer-brand .brand-square{background:#8a8a8a}
.footer-rule{position:absolute;left:102px;width:554px;height:1px;background:#4a4a4a}
.footer-nav{position:absolute;top:101px;left:0;width:757px}
.footer-nav a{position:absolute;font-family:"Montserrat",sans-serif;font-weight:600;font-size:6.8px;color:#888;text-decoration:none}
.footer-nav a.active{color:var(--green)}
.footer-col{position:absolute;top:139px}
.footer-col h3{font-family:"Montserrat",sans-serif;font-weight:700;font-size:8px;color:var(--orange);margin-bottom:9px}
.footer-col p{font-size:6.8px;color:var(--footer-text);line-height:14.4px}
.footer-col .hl{color:var(--green)}
.footer-col .wt{color:#ddd}
.addr{display:flex;gap:5px;font-size:6.8px;color:var(--footer-text);line-height:10.5px}
.phone{display:flex;gap:5px;align-items:center;font-size:7px;color:#eee;margin-top:9px;font-weight:600}
.badge{position:absolute;background:#5a5a5a}
</style>
</head>
<body>

<header class="site-header">
  <div class="brand"><span class="brand-square"></span>KR APPRAISALS</div>
  <nav class="main-nav">
    <a style="left:385px">HOME</a>
    <a class="active" style="left:432px">ABOUT</a>
    <a style="left:483px">SERVICES</a>
    <a style="left:543px">NEWS &amp; VIEWS</a>
    <a style="left:621px">CONTACT</a>
  </nav>
</header>

<h1 class="page-title">MEET THE TEAM</h1>

<section class="member" style="top:172px">
  <div class="member-photo" role="img" aria-label="Portrait photo of Martin Hale" style="background:linear-gradient(160deg,#f2ece6 0%,#d9b8a0 55%,#2a2e3a 100%)"></div>
  <div class="member-info">
    <h2 class="member-name">Martin Hale</h2>
    <p class="member-role">Managing Director</p>
    <p class="member-field">Business &amp; Intellectual Property Valuations</p>
    <p class="member-bio">Martin Hale (Netherlands) is a business and intangible asset valuation specialist with 20 years investment industry experience and more than 13 years valuation advisory and corporate finance experience. He has been involved in cross border valuation issues in America, Europe, Middle East, Central Asia and Africa. Martin is a CVF charterholder, IVS accredited senior appraiser in business valuation and Dutch Register of Valuation Experts accredited Register Valuator (RV). He is chairman of IVS Europe’s education committee, vice president of IVS Europe, serves on the Global Council of Business Appraisers (GCBA) Education &amp; Marketing Committees and in various voluntary roles at CVF Netherlands. Martin is a lecturer at Northgate University where he developed the CVF Level 1 prep program and appears as a guest lecturer at several Dutch universities on valuation topics.</p>
  </div>
</section>
<div class="divider" style="top:357px"></div>

<section class="member" style="top:390px">
  <div class="member-photo" role="img" aria-label="Black and white portrait photo of Joost van Dam" style="background:linear-gradient(160deg,#f0f0f0 0%,#bdbdbd 55%,#1e1e1e 100%)"></div>
  <div class="member-info">
    <h2 class="member-name">Joost van Dam</h2>
    <p class="member-field">Transfer Pricing</p>
    <p class="member-bio" style="margin-top:20px">Joost van Dam (Netherlands) has broad experience in international tax consulting since 1992, particularly in the transfer pricing area. He has been involved in numerous transfer pricing projects, e.g. IP (re)structuring, documentation, valuations, financial services and dispute resolution. Joost has written a number of articles for publications such as Global Pricing Review, Tax Practice Quarterly and Finance Leader Monthly. He has been named numerous times as one of the World’s Leading Transfer Pricing Advisors. Joost has taught transfer pricing and risk management courses for organizations such the Westbrook University and the Tax Academy Institute.</p>
  </div>
</section>
<div class="divider" style="top:546px"></div>

<section class="member" style="top:579px">
  <div class="member-photo" role="img" aria-label="Portrait photo of Glen Harper" style="background:linear-gradient(160deg,#6a6a6a 0%,#c98e6e 50%,#1f1f24 100%)"></div>
  <div class="member-info">
    <h2 class="member-name">Glen Harper</h2>
    <p class="member-field">Machinery &amp; Equipment Valuations</p>
    <p class="member-bio" style="margin-top:12px">Glen Harper (New York) is CEO of HG Appraisal and has 34 years experience with International valuation firms. He lived and worked in China, was CEO of a valuation business in Japan, and helped start an operation in Singapore. Glen is an IVS and MIVP designated valuer. He has an academic degree in Valuation Sciences from Bayview University, and is a frequent speaker and author on valuation topics worldwide. Glen serves on the Board of the Global Council of Business Appraisers (GCBA), and Chairs the GCBA Marketing Committee, is past editor of the IVS Machinery &amp; Technical Specialties Journal, and past member of IVP Americas Plant Machinery Committee.</p>
  </div>
</section>
<div class="divider" style="top:740px"></div>

<section class="member" style="top:773px">
  <div class="member-photo" role="img" aria-label="Portrait photo of Daniel Ko in front of a wooden wall" style="background:linear-gradient(160deg,#b07a60 0%,#8c5a46 45%,#24303a 100%)"></div>
  <div class="member-info">
    <h2 class="member-name">Daniel Ko</h2>
    <p class="member-bio" style="margin-top:12px">Daniel Ko is a specialist in fixed asset valuations which covers a broad range of applications including: insurance placement values, financial reporting, tax purposes, fixed asset leases, restructuring, acquisitions, and divestitures. He has performed valuation services since 2004 for companies with facilities across Europe, the Americas, Middle East, Africa, Asia, and Australia. He is a Registered Valuer of the Institute of Valuation Professionals (IVP) where he co-chairs the Machinery and Business Assets committee in the Netherlands.</p>
  </div>
</section>

<footer class="site-footer">
  <svg class="footer-bg" width="757" height="224" viewBox="0 0 757 224" aria-hidden="true">
    <polygon points="0,43 378.5,0 757,43 757,224 0,224" fill="#333"/>
  </svg>
  <div class="footer-brand"><span class="brand-square"></span>KR APPRAISALS</div>
  <div class="footer-rule" style="top:92px"></div>
  <nav class="footer-nav">
    <a class="active" style="left:243px">HOME</a>
    <a style="left:291px">ABOUT</a>
    <a style="left:341px">SERVICES</a>
    <a style="left:401px">NEWS &amp; VIEWS</a>
    <a style="left:479px">CONTACT</a>
  </nav>
  <div class="footer-rule" style="top:121px"></div>

  <div class="footer-col" style="left:103px">
    <h3>CREDITS</h3>
    <p>© 2019 <span class="hl">KR Appraisals</span></p>
    <p>Logo by <span class="wt">Lena Vos</span></p>
    <p>Website by <span class="hl">Brightline Studio</span></p>
  </div>

  <div class="footer-col" style="left:246px">
    <h3>LEIDEN</h3>
    <div class="addr">
      <svg width="6" height="9" viewBox="0 0 6 9" aria-hidden="true"><path d="M3 0C1.3 0 0 1.3 0 3c0 2.2 3 6 3 6s3-3.8 3-6C6 1.3 4.7 0 3 0zm0 4.2A1.2 1.2 0 1 1 3 1.8a1.2 1.2 0 0 1 0 2.4z" fill="#9bcb3c"/></svg>
      <span>Parkweg 14<br>2300 AA Leiden</span>
    </div>
    <div class="phone">
      <svg width="8" height="8" viewBox="0 0 8 8" aria-hidden="true"><path d="M1.6.2l1.2 1.6-.7 1c.5 1 1.3 1.8 2.3 2.3l1-.7 1.6 1.2-.6 1.4C3.6 7 1 4.4.2 2.4z" fill="#9bcb3c"/></svg>
      <span>070 555 0142</span>
    </div>
  </div>

  <div class="footer-col" style="left:389px">
    <h3>AMSTERDAM</h3>
    <div class="addr">
      <svg width="6" height="9" viewBox="0 0 6 9" aria-hidden="true"><path d="M3 0C1.3 0 0 1.3 0 3c0 2.2 3 6 3 6s3-3.8 3-6C6 1.3 4.7 0 3 0zm0 4.2A1.2 1.2 0 1 1 3 1.8a1.2 1.2 0 0 1 0 2.4z" fill="#9bcb3c"/></svg>
      <span>Havenstraat 8<br>1000 AB Amsterdam</span>
    </div>
    <div class="phone">
      <svg width="8" height="8" viewBox="0 0 8 8" aria-hidden="true"><path d="M1.6.2l1.2 1.6-.7 1c.5 1 1.3 1.8 2.3 2.3l1-.7 1.6 1.2-.6 1.4C3.6 7 1 4.4.2 2.4z" fill="#9bcb3c"/></svg>
      <span>020 555 0187</span>
    </div>
  </div>

  <div class="badge" role="img" aria-label="Partner certification badge" style="left:540px;top:133px;width:108px;height:22px;border-radius:3px"></div>
  <div class="badge" role="img" aria-label="Professional membership badge" style="left:539px;top:164px;width:108px;height:44px;border-radius:3px"></div>
</footer>

</body>
</html>
```